Business card for law firm

Need business card for new law firm. Think confident, authoritative, conservative, but not stuffy or old-fashioned.

Contact Information for Business Card

Content for card - logo (uploaded), plus the following:

Paul Whitcombe (larger font)
Managing Partner (larger font, but not as large as name)
Level 9, 7 Ferris Lane
Sydney NSW 2000
Main Tel 02 9364 2710
Direct Tel 02 8472 3159
Email paul@qvlegal.com.au
www.qvlegal.com.au

Letterhead design should include logo plus:
Level 9, 7 Ferris Lane
Sydney NSW 2000
Tel 02 8472 3159
www.qvlegal.com.au

```html
<!DOCTYPE html>
<html lang="en">
<head>
<meta charset="utf-8">
<title>Quayvale Legal — Business Card</title>
<link rel="stylesheet" href="https://fonts.googleapis.com/css2?family=Open+Sans:wght@400;700&display=swap">
<style>
  :root {
    --navy: #0c1f5a;
    --ink: #141414;
    --text: #2a2a2a;
    --rule: #c8c8c8;
    --paper: #ffffff;
    --backdrop: #dcdde0;
  }
  * { box-sizing: border-box; margin: 0; padding: 0; }
  html, body { width: 1200px; height: 1141px; overflow: hidden; }
  body {
    background: var(--backdrop);
    font-family: "Open Sans", Arial, sans-serif;
    color: var(--text);
    position: relative;
  }
  .card {
    position: absolute;
    left: 210px;
    width: 780px;
    height: 440px;
    background: var(--paper);
    border-radius: 36px;
    overflow: hidden;
    box-shadow: 0 2px 6px rgba(0,0,0,.15);
  }
  .card--front { top: 70px; }
  .card--back { top: 620px; }

  .swoosh { position: absolute; inset: 0; width: 100%; height: 100%; }

  .brand {
    position: absolute;
    display: flex;
    flex-direction: column;
    align-items: center;
    gap: 22px;
  }
  .brand__square { background: var(--navy); }
  .brand__name {
    font-weight: 400;
    color: var(--ink);
    letter-spacing: .12em;
    text-align: center;
    line-height: 1.1;
  }
  .card--front .brand { left: 60px; top: 80px; width: 320px; }
  .card--front .brand__square { width: 64px; height: 64px; }
  .card--front .brand__name { font-size: 34px; }

  .divider {
    position: absolute;
    left: 408px; top: 48px;
    width: 2px; height: 240px;
    background: var(--rule);
  }
  .details { position: absolute; left: 436px; top: 44px; }
  .details__name { font-size: 26px; font-weight: 700; color: var(--navy); text-transform: uppercase; }
  .details__role { font-size: 18px; text-transform: uppercase; margin-bottom: 16px; }
  .details__address { font-size: 19px; line-height: 1.4; margin-bottom: 14px; }
  .contact { list-style: none; font-size: 18px; line-height: 1.65; }
  .contact li { display: flex; align-items: center; gap: 8px; }
  .contact svg { width: 16px; height: 16px; flex: none; }

  .card--back .brand { left: 0; right: 0; top: 90px; }
  .card--back .brand__square { width: 84px; height: 84px; }
  .card--back .brand__name { font-size: 44px; }
  .web {
    position: absolute; left: 0; right: 0; top: 320px;
    text-align: center; font-size: 24px; letter-spacing: .18em; color: var(--ink);
  }
  .web strong { color: var(--navy); font-weight: 700; }
</style>
</head>
<body>

<section class="card card--front">
  <svg class="swoosh" viewBox="0 0 780 440" preserveAspectRatio="none" aria-hidden="true">
    <path d="M0,292 Q330,334 640,320 L780,250 L780,440 L0,440 Z" fill="var(--ink)"/>
    <path d="M0,340 Q360,340 722,298 L650,440 L0,440 Z" fill="var(--navy)" stroke="#fff" stroke-width="5"/>
  </svg>

  <div class="brand">
    <div class="brand__square"></div>
    <div class="brand__name">QUAYVALE LEGAL</div>
  </div>

  <div class="divider"></div>

  <div class="details">
    <p class="details__name">Paul Whitcombe</p>
    <p class="details__role">Managing Partner</p>
    <p class="details__address">Level 9, 7 Ferris Lane<br>Sydney NSW 2000</p>
    <ul class="contact">
      <li><svg viewBox="0 0 16 16"><circle cx="8" cy="8" r="7" fill="none" stroke="var(--navy)" stroke-width="1.5"/><path d="M5.5 4.5l2 2-1 1c.5 1 1.2 1.7 2 2l1-1 2 2-1 1.2C7.5 11.5 4.5 8.5 4.3 5.6z" fill="var(--navy)"/></svg>02 9364 2710(Main)</li>
      <li><svg viewBox="0 0 16 16"><circle cx="8" cy="8" r="7" fill="none" stroke="var(--navy)" stroke-width="1.5"/><path d="M5.5 4.5l2 2-1 1c.5 1 1.2 1.7 2 2l1-1 2 2-1 1.2C7.5 11.5 4.5 8.5 4.3 5.6z" fill="var(--navy)"/></svg>02 8472 3159(Direct)</li>
      <li><svg viewBox="0 0 16 16"><rect x="1.5" y="4" width="13" height="9" fill="var(--navy)"/><path d="M1.5 4l6.5 5 6.5-5" fill="none" stroke="#fff" stroke-width="1.2"/></svg>paul@qvlegal.com.au</li>
      <li><svg viewBox="0 0 16 16" fill="none" stroke="var(--navy)" stroke-width="1.3"><circle cx="8" cy="8" r="6.5"/><ellipse cx="8" cy="8" rx="3" ry="6.5"/><path d="M1.5 8h13M2.5 5h11M2.5 11h11"/></svg>www.qvlegal.com.au</li>
    </ul>
  </div>
</section>

<section class="card card--back">
  <div class="brand">
    <div class="brand__square"></div>
    <div class="brand__name">QUAYVALE LEGAL</div>
  </div>
  <p class="web">www.<strong>qvlegal</strong>.com.au</p>
</section>

</body>
</html>
```